Fernwick Landscaping Folder Design

I need a graphic designer to design a folder so we can insert informational sheets inside it for customers. The folder must include the company logo, project images, on front and back of folder and slogan " The Experience You Want, The Service You Expect, And The Value You Deserve'

Folder to also include phone numbers : 416 555 0193 as well as the website: www.fernwicklandscaping.example as well as we gurantee a 24 month warranty.

I have attached sample of size we need.

Pixel Harbor has also done something similar for me for Tollbridge Landscapes

Target Market(s)

geared toward home owners & commercial/industrial

Industry/Entity Type

Landscaping

Font styles to use
Other font styles liked:
• open to new trendy font

Requirements
Must have
• Telephone Number, email address, slogan, images,
Nice to have
• images of completed projects incorporated into the front and back of folder as well as the logo
Should not have
• n/a

```html
<!DOCTYPE html>
<html lang="en">
<head>
<meta charset="utf-8">
<title>Fernwick Landscaping Folder</title>
<link rel="stylesheet" href="https://fonts.googleapis.com/css2?family=Oswald:wght@400;700&family=Open+Sans:wght@600;700&display=swap">
<style>
  :root {
    --backdrop: #e6e4e0;
    --folder: #0c0c0c;
    --folder-edge: #1c1c1c;
    --type-soft: #262626;
    --type-strong: #353535;
    --mark: #5a5a5a;
    --accent: #4cb648;
    --accent-text: #5ecb58;
    --white: #ffffff;
    --stone: #9a968e;
    --lawn: #5f7046;
    --pool: #2a6fb0;
    --garage: #c9c0ae;
    --drive: #b9b6ae;
  }
  * { box-sizing: border-box; margin: 0; padding: 0; }
  html, body { width: 1200px; height: 848px; overflow: hidden; }
  body { background: var(--backdrop); position: relative; }

  .folder {
    position: absolute;
    top: 127px;
    width: 420px;
    height: 594px;
    background: var(--folder);
    border: 1px solid var(--folder-edge);
    box-shadow: 0 6px 18px rgba(0,0,0,0.25);
  }
  .folder--front { left: 150px; }
  .folder--back { left: 630px; }

  .slogan {
    position: absolute;
    left: 28px;
    top: 40px;
    font-family: "Oswald", sans-serif;
    text-transform: uppercase;
    font-size: 56px;
    line-height: 0.98;
    letter-spacing: 0.5px;
  }
  .slogan__line { display: block; }
  .slogan__line--soft { color: var(--type-soft); font-weight: 400; }
  .slogan__line--strong { color: var(--type-strong); font-weight: 700; }

  .brand {
    position: absolute;
    right: 30px;
    bottom: 60px;
    display: flex;
    align-items: center;
    gap: 10px;
    font-family: "Oswald", sans-serif;
    font-weight: 700;
    font-size: 22px;
    letter-spacing: 1px;
    text-transform: uppercase;
    color: var(--mark);
  }
  .brand__square { width: 14px; height: 14px; background: var(--mark); }

  .gallery {
    position: absolute;
    left: 48px;
    top: 36px;
    width: 324px;
    display: grid;
    grid-template-columns: 1fr 1fr;
    grid-template-rows: 128px 98px 120px;
    gap: 3px;
  }
  .gallery__photo { display: block; }
  .gallery__photo--wide { grid-column: 1 / 3; }
  .gallery__photo--patio { background: linear-gradient(135deg, var(--lawn), var(--stone) 60%, #d8d4cc); }
  .gallery__photo--pool { background: radial-gradient(ellipse at 60% 60%, var(--pool), #16324d 80%); }
  .gallery__photo--garage { background: linear-gradient(160deg, var(--garage), #8e8676); }
  .gallery__photo--drive { background: linear-gradient(180deg, #6f7d5a 0%, var(--lawn) 40%, var(--drive) 70%, #8e8b83); }

  .warranty {
    position: absolute;
    left: 48px;
    top: 388px;
    width: 324px;
    height: 24px;
    background: var(--accent);
    color: var(--white);
    font-family: "Open Sans", sans-serif;
    font-weight: 700;
    font-size: 9px;
    letter-spacing: 0.5px;
    text-transform: uppercase;
    display: flex;
    align-items: center;
    justify-content: center;
  }

  .contact {
    position: absolute;
    left: 48px;
    top: 424px;
    width: 324px;
    list-style: none;
    font-family: "Open Sans", sans-serif;
    font-weight: 600;
    font-size: 9.5px;
    color: var(--accent-text);
    padding-left: 60px;
  }
  .contact__item { display: flex; align-items: center; gap: 6px; margin-bottom: 5px; }
  .contact__icon { width: 9px; height: 9px; flex: none; }
</style>
</head>
<body>

<section class="folder folder--front" aria-label="Folder front cover">
  <h1 class="slogan">
    <span class="slogan__line slogan__line--soft">The Experience</span>
    <span class="slogan__line slogan__line--strong">You Want,</span>
    <span class="slogan__line slogan__line--soft">The Service</span>
    <span class="slogan__line slogan__line--strong">You Expect,</span>
    <span class="slogan__line slogan__line--soft">And The Value</span>
    <span class="slogan__line slogan__line--strong">You Deserve</span>
  </h1>
  <div class="brand">
    <span class="brand__square"></span>
    <span class="brand__name">Fernwick Landscaping</span>
  </div>
</section>

<section class="folder folder--back" aria-label="Folder back cover">
  <div class="gallery">
    <div class="gallery__photo gallery__photo--wide gallery__photo--patio" role="img" aria-label="Photo of a stone patio and walkway with garden plantings"></div>
    <div class="gallery__photo gallery__photo--pool" role="img" aria-label="Photo of a lit backyard pool at night"></div>
    <div class="gallery__photo gallery__photo--garage" role="img" aria-label="Photo of an interlock driveway in front of a garage"></div>
    <div class="gallery__photo gallery__photo--wide gallery__photo--drive" role="img" aria-label="Photo of a curved paved driveway with lawn and trees"></div>
  </div>

  <div class="warranty">We gurantee a 24 month warranty</div>

  <ul class="contact">
    <li class="contact__item">
      <svg class="contact__icon" viewBox="0 0 10 10" aria-hidden="true">
        <circle cx="5" cy="5" r="5" fill="var(--accent-text)"/>
        <path d="M3.2 2.6 L4.1 2.4 L4.6 3.7 L4 4.2 Q4.6 5.5 5.8 6 L6.3 5.4 L7.6 5.9 L7.4 6.8 Q5.8 7.6 3.9 5.9 Q2.5 4.3 3.2 2.6Z" fill="var(--folder)"/>
      </svg>
      <span>416 555 0193</span>
    </li>
    <li class="contact__item">
      <svg class="contact__icon" viewBox="0 0 10 10" aria-hidden="true">
        <circle cx="5" cy="5" r="5" fill="var(--accent-text)"/>
        <circle cx="5" cy="5" r="3" fill="none" stroke="var(--folder)" stroke-width="0.8"/>
        <path d="M2 5 H8 M5 2 Q3.4 5 5 8 M5 2 Q6.6 5 5 8" fill="none" stroke="var(--folder)" stroke-width="0.7"/>
      </svg>
      <span>www.fernwicklandscaping.example</span>
    </li>
  </ul>
</section>

</body>
</html>
```